Simple Recipe eBook

I need the graphic work done for a simple recipe ebook, I have attached all of the required information for it, as well as our company logo. Further company info can be found at velorabix.com

I would like each recipe page to include 2 recipes, each recipe needs to include ingredients, picture, method, and nutritional info.

I would like the style to appear fresh and healthy, with lots of graphics and colours to match.
Please let me know if you need any guidance

Target Market(s)

Females aged from 15-25

Industry/Entity Type

It Company

```html
<!DOCTYPE html>
<html lang="en">
<head>
<meta charset="utf-8">
<title>Breakfast Recipes</title>
<link rel="stylesheet" href="https://fonts.googleapis.com/css2?family=Comfortaa:wght@400&family=Quicksand:wght@300;400;500;600&family=Open+Sans:wght@400;600;700&display=swap">
<style>
  :root {
    --teal: #22c9c6;
    --teal-deep: #18b8b5;
    --ink: #2b2b2b;
    --white: #ffffff;
    --grey-box: #d9d9d9;
    --edge: #9a9a9a;
  }
  * { box-sizing: border-box; margin: 0; padding: 0; }
  html, body { width: 848px; height: 1200px; overflow: hidden; background: var(--white); }
  .page {
    position: relative;
    width: 848px;
    height: 1200px;
    background: var(--white);
    border-right: 1px solid var(--edge);
    font-family: "Open Sans", sans-serif;
    color: var(--ink);
  }
  .page-title {
    position: absolute;
    top: 14px; left: 0; width: 100%;
    text-align: center;
    font-family: "Comfortaa", sans-serif;
    font-size: 70px;
    color: var(--teal);
    letter-spacing: 1px;
    line-height: 1;
  }
  .side-panel {
    position: absolute;
    left: 425px; top: 117px;
    width: 423px; height: 1083px;
    background: var(--teal);
  }
  .recipe { position: absolute; top: 117px; }
  .recipe--eggs { left: 46px; width: 366px; }
  .recipe--smoothie { left: 469px; width: 368px; color: var(--white); }
  .recipe-name {
    height: 90px;
    display: flex; align-items: center; justify-content: center;
    text-align: center;
    font-family: "Quicksand", sans-serif;
    font-weight: 500;
    font-size: 23px;
    line-height: 1.4;
    text-transform: uppercase;
    color: var(--ink);
    width: 333px;
  }
  .recipe--smoothie .recipe-name { color: var(--white); height: 80px; padding-top: 2px; }
  .recipe-photo { display: block; width: 333px; height: 218px; }
  .recipe--smoothie .recipe-photo { margin-top: 10px; width: 333px; height: 221px; }
  .section-head {
    font-family: "Quicksand", sans-serif;
    font-weight: 400;
    font-size: 31px;
    line-height: 1;
    letter-spacing: 0.5px;
    text-transform: uppercase;
    margin-top: 8px;
  }
  .recipe--smoothie .section-head { color: var(--white); }
  .nutrition {
    width: 333px;
    height: 122px;
    margin-top: 2px;
    padding: 8px 6px 4px;
    font-size: 10px;
    line-height: 15px;
    letter-spacing: -0.2px;
  }
  .nutrition--teal { background: var(--teal-deep); color: var(--white); }
  .nutrition--grey { background: var(--grey-box); color: var(--ink); width: 339px; height: 120px; }
  .nutrition-grid {
    display: grid;
    grid-template-columns: 100px 74px 76px 1fr;
  }
  .nutrition-grid span { white-space: nowrap; }
  .nutrition-note { font-style: italic; font-size: 9.5px; margin-top: 6px; padding-left: 4px; white-space: nowrap; }
  .ingredients { list-style: none; font-size: 12.5px; line-height: 21px; margin-top: 6px; }
  .recipe--smoothie .ingredients { font-weight: 700; font-size: 12px; }
  .method { margin-top: 6px; font-size: 12.5px; line-height: 18.5px; }
  .method-step { font-weight: 700; color: var(--teal); font-size: 13px; }
  .recipe--smoothie .method { font-size: 12px; }
  .recipe--smoothie .method-step { color: var(--white); }
  .recipe--smoothie .method p { font-weight: 700; }
</style>
</head>
<body>
<div class="page">
  <h1 class="page-title">breakfast</h1>
  <div class="side-panel"></div>

  <section class="recipe recipe--eggs">
    <h2 class="recipe-name">Pesto scrambled eggs<br>with spinach &amp; avocado</h2>
    <svg class="recipe-photo" role="img" aria-label="Photo of pesto scrambled eggs with avocado slices and spinach on whole grain toast" viewBox="0 0 333 218">
      <defs>
        <radialGradient id="eggsTone" cx="50%" cy="45%" r="65%">
          <stop offset="0" stop-color="#e9c27a"/>
          <stop offset="0.45" stop-color="#b9a27a"/>
          <stop offset="1" stop-color="#f4f3ef"/>
        </radialGradient>
      </defs>
      <rect width="333" height="218" fill="url(#eggsTone)"/>
    </svg>
    <h3 class="section-head">Nutritions</h3>
    <div class="nutrition nutrition--teal">
      <div class="nutrition-grid">
        <span>Energy</span><span>1750kJ</span><span>Dietary Fibre</span><span>4.50g</span>
        <span>Fat saturated</span><span>7.50g</span><span>Protein</span><span>19.00g</span>
        <span>Fat Total</span><span>32.00g</span><span>Cholesterol</span><span>365.00mg</span>
        <span>Carbohydratesugar</span><span>2.50g</span><span>Sodium</span><span>420.00mg</span>
        <span>Carbohydrate Total</span><span>16.00g</span><span></span><span></span>
      </div>
      <p class="nutrition-note">All nutrition values are per serve.</p>
    </div>
    <h3 class="section-head">Ingredients</h3>
    <ul class="ingredients">
      <li>4 eggs</li>
      <li>2 tablespoons milk</li>
      <li>75g baby spinach leaves</li>
      <li>1 tablespoon basil pesto, plus extra to serve Olive oil spray</li>
      <li>1/2 large firm ripe avocado, stone removed,chopped</li>
      <li>2 slices whole grain toast, to serve</li>
    </ul>
    <h3 class="section-head">Recepie</h3>
    <div class="method">
      <p class="method-step">Step 1</p>
      <p>Whisk the eggs and milk together in a medium size bowl, season with salt and pepper. Heat a medium size frying pan over a medium heat and spray lightly with olive oil spray.</p>
      <p class="method-step">Step 2</p>
      <p>Add the baby spinach leaves, cook stirring, until just wilted. Remove from pan.</p>
      <p class="method-step">Step 3</p>
      <p>Return pan to a medium heat, spray with a little more oil. Add egg mixture and using a wooden spoon, stir and bring the egg mixture on the edge of the pan to the centre. Continue until the eggs are almost set, add the pesto and baby spinach, and stir until just combined. Season to taste with sea salt and freshly ground black pepper. Serve immediately with toast, chopped avocado and an extra dollop of pesto if desired.</p>
    </div>
  </section>

  <section class="recipe recipe--smoothie">
    <h2 class="recipe-name">Power smoothie</h2>
    <svg class="recipe-photo" role="img" aria-label="Photo of a green smoothie in a glass with a striped straw" viewBox="0 0 333 221">
      <defs>
        <linearGradient id="smoothieTone" x1="0" y1="0" x2="0" y2="1">
          <stop offset="0" stop-color="#f3f3f1"/>
          <stop offset="0.4" stop-color="#9fae94"/>
          <stop offset="1" stop-color="#6f8a6a"/>
        </linearGradient>
      </defs>
      <rect width="333" height="221" fill="url(#smoothieTone)"/>
    </svg>
    <h3 class="section-head">Nutritions</h3>
    <div class="nutrition nutrition--grey">
      <div class="nutrition-grid">
        <span>Energy</span><span>1463kJ</span><span>Dietary Fibre</span><span>g</span>
        <span>Fat saturated</span><span>4.00g</span><span>Protein</span><span>14.00g</span>
        <span>Fat Total</span><span>7.00g</span><span>Cholesterol</span><span>mg</span>
        <span>Carbohydratesugar</span><span>44.00g</span><span>Sodium</span><span>118.60mg</span>
        <span>Carbohydrate Total</span><span>5.00g</span><span></span><span></span>
      </div>
      <p class="nutrition-note">All nutrition values are per serve.</p>
    </div>
    <h3 class="section-head">Ingredients</h3>
    <ul class="ingredients">
      <li>2 large ripe bananas, roughly chopped</li>
      <li>1/2 cup reduced-fat plain yoghurt</li>
      <li>2 tablespoons rolled oats</li>
      <li>1 tablespoon Verdalis Natural Super Greens powder (see note)</li>
      <li>2 teaspoons honey (optional)</li>
      <li>1 1/2 cups reduced-fat milk</li>
    </ul>
    <h3 class="section-head">Recepie</h3>
    <div class="method">
      <p class="method-step">Step 1</p>
      <p>Blend banana, yoghurt, rolled oats, super greens, honey (if using) and milk together until smooth. Pour into chilled glasses. Serve.</p>
    </div>
  </section>
</div>
</body>
</html>
```